Set up small scale company website

We need a website set up for our educational consultancy - Vexmore Education. We like the following site and want something similar www.plindarhub.co.uk We can provide the copy and images but need the following:- setting up the overall theme and design - to our requirements on colours and forma- Approximately 4 pages of services offered and with an index pageEtct (yellow and green)And the following pages - as well as a home page:- A contact page linked to our email addresses and registered business address 17 Wexbury Lane, Harwich, Essex, CO14 8PN- About Us page - An index of services page that links to between 4-6 pages outlining services- A News page that links to updates of latest services, events and activities - easily updated by usOn the homepage we'd like links to chirpnet and WorkLoop feeds and links to our other blogs and websites
Target Market(s)
Schools, local authoroties and multi-academy trusts
Logo Text
Vexmore Education
Coding
Coded - Design and coding required
Number of Pages Required
5+ page
Font styles to use
Requirements
Should not have
- No tacky pictures of mortar boards or chalk boards etc.

```html
<!DOCTYPE html>
<html lang="en">
<head>
<meta charset="utf-8">
<title>Vexmore Education – Centralising Finance and Operations</title>
<link href="https://fonts.googleapis.com/css2?family=Montserrat:wght@400;500;600;700&family=Open+Sans:wght@400;600&family=Roboto:wght@400&display=swap" rel="stylesheet">
<style>
:root{
  --green:#8dc63f;
  --nav-active:#1a8a6a;
  --yellow:#f5e52b;
  --ink:#1a1a1a;
  --body:#555;
  --grey-bg:#f4f4f4;
  --footer:#0f1e2c;
  --link:#2aa3d6;
  --chirp:#2aa3d6;
  --work:#1451a6;
}
*{margin:0;padding:0;box-sizing:border-box}
html,body{width:1000px;height:1200px;overflow:hidden;background:#fff}
body{position:relative;font-family:"Open Sans",sans-serif;color:var(--body)}
.abs{position:absolute}

.site-header{position:absolute;left:0;top:0;width:1000px;height:84px;border-bottom:5px solid var(--green)}
.brand{position:absolute;left:120px;top:20px;display:flex;align-items:center;gap:10px}
.brand-dot{width:36px;height:36px;border-radius:50%;background:var(--green)}
.brand-name{font-family:"Montserrat",sans-serif;font-weight:700;font-size:21px;color:var(--ink);letter-spacing:-.5px;white-space:nowrap}
.main-nav{position:absolute;right:120px;top:32px;display:flex;gap:31px;font-family:"Montserrat",sans-serif;font-size:13px;color:#666}
.main-nav .active{color:var(--nav-active)}

.service-title{left:120px;top:152px;font-family:"Montserrat",sans-serif;font-weight:600;font-size:28px;color:var(--green)}
.service-copy{left:121px;top:198px;width:510px;font-size:11.5px;line-height:19px}
.service-copy p{margin-bottom:8px}
.service-photo{left:677px;top:151px;width:203px;height:203px;border-radius:50%;border:4px solid var(--green);background:linear-gradient(135deg,#9aa3ad,#e4e7ea 55%,#6d5a4a)}
.checklist{left:120px;top:318px;list-style:none;font-family:"Montserrat",sans-serif;font-size:16.5px;color:var(--ink)}
.checklist li{display:flex;align-items:center;height:33.4px}
.checklist svg{margin-right:11px}
.contact-note{left:120px;top:464px;font-size:12px}
.contact-btn{left:120px;top:485px;height:37px;padding:0 24px;border-radius:19px;background:var(--yellow);font-family:"Montserrat",sans-serif;font-weight:600;font-size:11.5px;color:var(--ink);display:flex;align-items:center;justify-content:center;white-space:nowrap}

.feed-band{left:0;top:585px;width:1000px;height:375px}
.feed-card{top:690px;width:168px;min-height:210px;background:#fff;box-shadow:0 1px 4px rgba(0,0,0,.12);padding:17px 13px 14px}
.feed-card p{font-size:11px;line-height:20px;color:#666}
.feed-card .handle-link{color:var(--link)}
.feed-card .url{display:block;margin-top:1px;color:var(--link)}
.feed-card .url.green{color:var(--green)}
.feed-card hr{border:0;border-top:2px solid #ddd;margin:12px 0 12px}
.feed-meta{display:flex;align-items:center;gap:9px}
.feed-icon{width:27px;height:27px;border-radius:50%;flex:none}
.feed-icon.chirp{background:var(--chirp)}
.feed-icon.work{background:var(--work)}
.feed-meta b{display:block;font-family:"Roboto",sans-serif;font-weight:400;font-size:12.5px;line-height:16px;color:#555}
.feed-meta span{display:block;font-family:"Roboto",sans-serif;font-size:8px;line-height:12px;color:#333}

.site-footer{left:0;top:960px;width:1000px;height:240px;background:var(--footer);color:#c9d0d8;font-size:9px}
.footer-head{position:absolute;top:36px;font-family:"Montserrat",sans-serif;font-weight:600;font-size:14px;color:var(--yellow)}
.footer-links{position:absolute;top:73px;display:grid;grid-template-columns:60px auto;row-gap:8px;line-height:12px}
.contact-info{position:absolute;left:313px;top:72px;list-style:none;line-height:12px}
.contact-info li{display:flex;gap:10px;margin-bottom:8px}
.contact-info svg{flex:none;margin-top:2px}
.newsletter{position:absolute;left:546px;top:70px;width:181px;height:33px;background:#f0f0f0;border-radius:2px;display:flex;align-items:center;justify-content:space-between;padding:0 9px 0 12px;color:#333;font-size:9px}
.socials{position:absolute;left:766px;top:70px;display:flex;gap:7px}
.socials span{width:33px;height:33px;border:1px solid #8a96a3;border-radius:50%;display:flex;align-items:center;justify-content:center;font-family:"Open Sans",sans-serif;font-weight:600;font-size:13px;color:#c9d0d8}
.footer-rule{position:absolute;left:120px;top:177px;width:760px;border-top:1px solid #3a4a5a}
.copyright{position:absolute;left:0;top:204px;width:1000px;text-align:center;font-size:10px;color:#aab3bd}
</style>
</head>
<body>

<header class="site-header">
  <div class="brand"><span class="brand-dot"></span><span class="brand-name">VEXMORE EDUCATION</span></div>
  <nav class="main-nav"><span>HOME</span><span class="active">SERVICES</span><span>NEWS</span><span>ABOUT US</span><span>CONTACT US</span></nav>
</header>

<h1 class="abs service-title">Centralising Finance and Operations</h1>
<div class="abs service-copy">
  <p>We can advise and support on the centralisation of finance and operations in Multi-Academy Trusts. Our systems are bespoke and devised in partnership with the trust and individual academies to ensure that they are fit for purpose.</p>
  <p>We can offer a full design and implementation service led by one of our consultants or support and advice with the centralisation process.</p>
</div>
<div class="abs service-photo" role="img" aria-label="Photo of hands working at a laptop and calculator over financial charts"></div>

<ul class="abs checklist">
  <li><svg width="14" height="11" viewBox="0 0 14 11"><path d="M1 5.5l4 4 8-8" fill="none" stroke="#333" stroke-width="3"/></svg>Viability Business Case</li>
  <li><svg width="14" height="11" viewBox="0 0 14 11"><path d="M1 5.5l4 4 8-8" fill="none" stroke="#333" stroke-width="3"/></svg>Bespoke centralisation design</li>
  <li><svg width="14" height="11" viewBox="0 0 14 11"><path d="M1 5.5l4 4 8-8" fill="none" stroke="#333" stroke-width="3"/></svg>Set up of finance systems</li>
  <li><svg width="14" height="11" viewBox="0 0 14 11"><path d="M1 5.5l4 4 8-8" fill="none" stroke="#333" stroke-width="3"/></svg>Training of school and central staff</li>
</ul>
<p class="abs contact-note">Please contact us for further details:</p>
<div class="abs contact-btn">office@vexmoreedu.com</div>

<svg class="abs feed-band" viewBox="0 0 1000 375" preserveAspectRatio="none"><path d="M0 70 Q500 -60 1000 70 V375 H0Z" fill="var(--grey-bg)"/></svg>

<article class="abs feed-card" style="left:120px">
  <p>Lorem ipsum dolor it amet, consectetur adipiscing its sed do <span class="handle-link">@vexmore-edu</span> tempor incididunt ut labore et dolore magna <span class="url">https://lorempage.com</span></p>
  <hr><div class="feed-meta"><i class="feed-icon chirp"></i><div><b>@vexmoreedu.</b><span>5 hour ago</span></div></div>
</article>
<article class="abs feed-card" style="left:317px">
  <p>Lorem ipsum dolor it amet, consectetur adipiscing its sed do <span class="handle-link">@vexmore-edu</span> tempor incididunt ut labore et dolore magna <span class="url">https://lorempage.com</span></p>
  <hr><div class="feed-meta"><i class="feed-icon work"></i><div><b>@vexmoreedu.</b><span>5 hour ago</span></div></div>
</article>
<article class="abs feed-card" style="left:515px">
  <p>Lorem ipsum dolor it amet, consectetur adipiscing its sed do <span class="handle-link">@vexmore-edu</span> tempor incididunt ut labore et dolore magna <span class="url green">https://lorempage.com</span></p>
  <hr><div class="feed-meta"><i class="feed-icon chirp"></i><div><b>@vexmoreedu.</b><span>5 hour ago</span></div></div>
</article>
<article class="abs feed-card" style="left:712px">
  <p>Lorem ipsum dolor it amet, consectetur adipiscing its sed do <span class="handle-link">@vexmore-edu</span> tempor incididunt ut labore et dolore magna <span class="url">https://lorempage.com</span></p>
  <hr><div class="feed-meta"><i class="feed-icon work"></i><div><b>@vexmoreedu.</b><span>5 hour ago</span></div></div>
</article>

<footer class="abs site-footer">
  <h3 class="footer-head" style="left:120px">Links</h3>
  <div class="footer-links" style="left:120px"><span>Home</span><span>Contact us</span><span>Services</span><span>Terms and Condition</span><span>News</span><span>Privacy Policy</span><span>About us</span><span></span></div>

  <h3 class="footer-head" style="left:313px">Contact info</h3>
  <ul class="contact-info">
    <li><svg width="7" height="9" viewBox="0 0 7 9"><path d="M3.5 0a3.5 3.5 0 0 0-3.5 3.5C0 6 3.5 9 3.5 9S7 6 7 3.5A3.5 3.5 0 0 0 3.5 0z" fill="#aab3bd"/><circle cx="3.5" cy="3.5" r="1.2" fill="var(--footer)"/></svg><span>Mr. Alan Brecket,<br>17 Wexbury Lane, Harwich, Essex, CO14 8PN</span></li>
    <li><svg width="8" height="8" viewBox="0 0 8 8"><path d="M1 0l2 2-1 1.2a5 5 0 0 0 2.8 2.8L6 5l2 2-1 1C3.5 8 0 4.5 0 1z" fill="#aab3bd"/></svg><span>Phone : 546 209 7713</span></li>
    <li><svg width="9" height="7" viewBox="0 0 9 7"><rect width="9" height="7" fill="#aab3bd"/><path d="M0 0l4.5 3.5L9 0" fill="none" stroke="var(--footer)"/></svg><span>Email : info@vexmoremail.com</span></li>
  </ul>

  <h3 class="footer-head" style="left:545px">Newsletter</h3>
  <div class="newsletter"><span>Email Address</span><svg width="16" height="12" viewBox="0 0 16 12"><rect width="16" height="12" rx="1.5" fill="#222"/><path d="M1 1.5l7 5 7-5" fill="none" stroke="#f0f0f0" stroke-width="1.5"/></svg></div>

  <h3 class="footer-head" style="left:766px">Follow us on</h3>
  <div class="socials"><span aria-label="Friendspace">F</span><span aria-label="chirpnet">C</span><span aria-label="WorkLoop">W</span></div>

  <div class="footer-rule"></div>
  <p class="copyright">Copyright &copy; 2019 &nbsp;Vexmore Education. &nbsp;All rights reserved.</p>
</footer>

</body>
</html>
```